Vantoq Business Card Project showing the logo and a marbo image on the rear

Design a whacky but professional business card, the logo is for the front and the Marbo image is for the rear. Happy to consider other open source Marbo Images if the designer wants to select one from the web. Vantoq is a competitor to OMB.com.au and Pellory.com.au and is based around every property in Australia

Target Market(s)

Business

Contact Information for Business Card

Name, Title, Email, Web, Phone Number

Font styles to use
Other font styles liked:
• avenir

Requirements
Must have
• Image on Back logo on front
Nice to have
• Happy to consider other images on rear, preftably Colin Marbo. Image supplied I own, we can use open source other Marbo Images

```html
<!DOCTYPE html>
<html lang="en">
<head>
<meta charset="utf-8">
<title>Vantoq Business Card</title>
<link rel="stylesheet" href="https://fonts.googleapis.com/css2?family=Catamaran:wght@600;700&family=Roboto:wght@400&display=swap">
<style>
  :root {
    --backdrop: #1f1f20;
    --orange: #ef8a0e;
    --ink: #111111;
    --card-black: #0b0b0b;
    --paper: #f4f4f4;
    --paper-shade: #e4e4e4;
    --night: #3c3d40;
    --text-light: #f2f2f2;
  }
  * { margin: 0; padding: 0; box-sizing: border-box; }
  html, body { width: 1138px; height: 1200px; overflow: hidden; }
  body { background: var(--backdrop); position: relative; font-family: "Roboto", Arial, sans-serif; }

  .card { position: absolute; border-radius: 16px; overflow: hidden; }

  .card-back { left: 156px; top: 276px; width: 374px; height: 618px; }
  .artwork {
    width: 100%; height: 100%;
    background:
      linear-gradient(180deg, transparent 0%, transparent 52%, #d94b9a 68%, #e7d43a 84%, #6cc4d6 94%, #7cc23a 100%),
      linear-gradient(90deg, var(--orange) 0%, var(--orange) 50%, var(--night) 50%, var(--night) 100%);
  }

  .card-front { left: 577px; top: 274px; width: 375px; height: 622px; background: var(--card-black); }
  .front-header { position: absolute; left: 0; top: 0; width: 375px; height: 300px; }

  .brand {
    position: absolute; left: 0; top: 150px; width: 100%;
    display: flex; justify-content: center; align-items: center; gap: 12px;
  }
  .brand-mark { width: 22px; height: 22px; background: var(--orange); }
  .brand-name {
    font-family: "Catamaran", "Avenir", sans-serif; font-weight: 700;
    font-size: 40px; color: var(--ink); line-height: 1;
  }

  .person { position: absolute; left: 0; width: 100%; text-align: center; }
  .person-name {
    top: 323px; font-family: "Catamaran", "Avenir", sans-serif; font-weight: 700;
    font-size: 26px; color: var(--orange); line-height: 1.2;
  }
  .person-title { top: 359px; font-size: 16px; color: var(--text-light); }

  .icon-row { position: absolute; left: 0; top: 410px; width: 375px; height: 30px; }

  .contact { position: absolute; left: 0; width: 100%; text-align: center; font-size: 16px; line-height: 23.5px; color: var(--text-light); }
  .contact-lines { top: 448px; }
  .contact-address { top: 538px; }
  .accent { color: var(--orange); }
</style>
</head>
<body>

  <section class="card card-back">
    <div class="artwork" role="img" aria-label="Colourful hand-drawn city illustration: a day sky and night sky over cheerful buildings with a train along the bottom"></div>
  </section>

  <section class="card card-front">
    <svg class="front-header" viewBox="0 0 375 300" aria-hidden="true">
      <defs>
        <linearGradient id="paperTone" x1="0" y1="0" x2="1" y2="0">
          <stop offset="0" stop-color="var(--paper-shade)"/>
          <stop offset="0.5" stop-color="var(--paper)"/>
          <stop offset="1" stop-color="var(--paper-shade)"/>
        </linearGradient>
      </defs>
      <path d="M0,222 C60,262 120,290 185,288 C260,286 320,258 375,222 V208 H0 Z" fill="var(--orange)"/>
      <path d="M0,0 H375 V208 C320,248 255,276 185,278 C115,280 55,252 0,214 Z" fill="url(#paperTone)"/>
    </svg>

    <div class="brand">
      <span class="brand-mark"></span>
      <span class="brand-name">Vantoq</span>
    </div>

    <h1 class="person person-name">Owen Tralley</h1>
    <p class="person person-title">Founder &amp; CEO</p>

    <svg class="icon-row" viewBox="0 0 375 30" aria-hidden="true">
      <g stroke="var(--orange)" fill="none">
        <line x1="59" y1="15" x2="131" y2="15" stroke-width="2"/>
        <line x1="246" y1="15" x2="318" y2="15" stroke-width="2"/>
        <circle cx="157" cy="15" r="13" stroke-width="2"/>
        <circle cx="187" cy="15" r="13" stroke-width="2"/>
        <circle cx="218" cy="15" r="13" stroke-width="2"/>
        <path d="M150,20 h14 v-4 l-3,-4 h-8 l-3,4 z M152,12 q5,-5 10,0" stroke-width="1.6"/>
        <rect x="180" y="10" width="14" height="10" stroke-width="1.6"/>
        <path d="M180,10 l7,6 l7,-6" stroke-width="1.6"/>
        <circle cx="218" cy="15" r="7" stroke-width="1.6"/>
        <path d="M211,15 h14 M218,8 q-4,7 0,14 M218,8 q4,7 0,14" stroke-width="1.3"/>
      </g>
    </svg>

    <div class="contact contact-lines">
      <p>(00) 4815 7260</p>
      <p>tralley@vantoq.com</p>
      <p>www.<span class="accent">vantoq</span>.com</p>
    </div>
    <div class="contact contact-address">
      <p>Level 4, 18 Ferren Lane,</p>
      <p>Sydney 2000, Australia</p>
    </div>
  </section>

</body>
</html>
```